"Vine Hollow Excursions" is a top notch Santa Barbara County Wine Tour company.

We provide scenic, boutique and custom wine tours. I need the card to be clean and classy. I will provide our logo. I would like the logo to cover the back side of the card as an option and would like to see a couple color options other then our signature green and gold. I would like to see some creative options and let the designers come up with options.
I need cards for myself and my team. The final design should communicate "An authentic and boutique wine tour experience"
Please use my website for reference www.vinehollowexcursions.example

Target Market(s)

We have a wide range of clients from millennials to baby boomers

Industry/Entity Type

Tour

Contact Information for Business Card

Contact info:
Dale Morton
805-219-6384
info@vinehollowexcursions.example
vinehollowexcursions.example

Colors

Designer to choose colors to be used in the design.

Requirements
Must have
• my logo
Nice to have
• *I would like to have the backside side with the logo and the company statement
• "An authentic and boutique wine tour experience" as an option.
• *I would also like to see what the designers can create!
• *I would like to see an option that incorporates or social: instagram, yelp, trip advisor
Should not have
• I do not want it too busy.

```html
<!DOCTYPE html>
<html lang="en">
<head>
<meta charset="utf-8">
<title>Vine Hollow Excursions – Business Card</title>
<link rel="stylesheet" href="https://fonts.googleapis.com/css2?family=Marcellus+SC&family=Open+Sans:wght@400&display=swap">
<style>
  :root {
    --backdrop: #eeeeef;
    --card-white: #fbfbfa;
    --vine-green: #266b46;
    --ink-grey: #4a4a4a;
    --cream: #ffffff;
    --social-red: #d8322b;
    --social-dark: #1e1e1e;
  }
  * { box-sizing: border-box; margin: 0; padding: 0; }
  html, body {
    width: 1200px; height: 900px; overflow: hidden;
    background: var(--backdrop);
  }
  .card-set { position: relative; width: 1200px; height: 900px; }
  .card {
    position: absolute; top: 300px;
    width: 525px; height: 300px;
    box-shadow: 0 6px 18px rgba(0,0,0,0.12);
  }
  /* Front */
  .card-front { left: 60px; background: var(--card-white); }
  .holder-name {
    position: absolute; left: 36px; top: 34px;
    font-family: "Marcellus SC", serif; font-size: 20px;
    color: var(--vine-green); letter-spacing: 0.5px;
  }
  .contact-list {
    position: absolute; left: 36px; top: 128px;
    list-style: none;
    font-family: "Open Sans", sans-serif; font-size: 12px;
    color: var(--ink-grey); line-height: 21px;
  }
  .contact-list li { display: flex; align-items: center; gap: 7px; white-space: nowrap; }
  .contact-icon { width: 10px; height: 10px; flex: none; }
  .brand-lockup {
    position: absolute; left: 296px; top: 112px; width: 200px;
    display: flex; align-items: center; gap: 12px;
  }
  .brand-mark {
    width: 48px; height: 48px; border-radius: 50%;
    background: var(--vine-green); flex: none;
  }
  .brand-name {
    font-family: "Marcellus SC", serif; font-size: 21px; line-height: 25px;
    color: var(--vine-green);
  }
  .social-row {
    position: absolute; right: 60px; bottom: 36px;
    display: flex; gap: 14px;
  }
  .social-badge { width: 28px; height: 28px; }
  .social-badge.round { border-radius: 50%; background: var(--social-red); }
  .social-badge.round-dark { border-radius: 50%; background: var(--social-dark); }
  .social-badge.square { border-radius: 6px; background: var(--social-dark); }
  /* Back */
  .card-back {
    left: 615px; background: var(--vine-green);
    display: flex; align-items: center; justify-content: center;
  }
  .statement {
    font-family: "Marcellus SC", serif; font-size: 27px; line-height: 34px;
    color: var(--cream); text-align: left; letter-spacing: 1px;
  }
</style>
</head>
<body>
<main class="card-set">
  <section class="card card-front">
    <p class="holder-name">Dale Morton</p>
    <ul class="contact-list">
      <li>
        <svg class="contact-icon" viewBox="0 0 12 12"><path fill="#266b46" d="M2 1h2.5l1 3-1.5 1a7 7 0 0 0 3 3l1-1.5 3 1V10a1 1 0 0 1-1 1A9 9 0 0 1 1 2a1 1 0 0 1 1-1z"/></svg>
        805-219-6384
      </li>
      <li>
        <svg class="contact-icon" viewBox="0 0 12 12"><rect x="0.5" y="2" width="11" height="8" rx="1" fill="#266b46"/><path d="M1 3l5 4 5-4" stroke="#fff" stroke-width="1" fill="none"/></svg>
        info@vinehollowexcursions.example
      </li>
      <li>
        <svg class="contact-icon" viewBox="0 0 12 12"><circle cx="6" cy="6" r="5.5" fill="#266b46"/><path d="M0.5 6h11M6 0.5c-3 3-3 8 0 11M6 0.5c3 3 3 8 0 11" stroke="#fff" stroke-width="0.8" fill="none"/></svg>
        vinehollowexcursions.example
      </li>
    </ul>
    <div class="brand-lockup">
      <span class="brand-mark"></span>
      <span class="brand-name">Vine Hollow<br>Excursions</span>
    </div>
    <div class="social-row" aria-label="Social listings">
      <span class="social-badge round"></span>
      <span class="social-badge round-dark"></span>
      <span class="social-badge square"></span>
    </div>
  </section>
  <section class="card card-back">
    <p class="statement">An authentic<br>and boutique<br>wine tour<br>experience</p>
  </section>
</main>
</body>
</html>
```